Business Card for Health Food Store

I need a business card for a health food store that includes the following information.

=========
FRONT
=========

***White background***

Bright Harvest (logo)
Supplements - Health Foods - Remedies

2214 Alder Rd.
Linden Falls, CA 95012
(corner of Ferris Ln.)

707-482-3196

BrightHarvest.co
BrightHarvestGoods@mailbox-example.com

On the right side of the front of the card, use a circle type seal with 25 large in the middle. Put the dates below it.
"Celebrating 25 Years"
1999 - 2024

*DO NOT USE A PERSON'S NAME ON THE CARD*

==========
BACK
==========

***Green background***

Full logo in white along with the social logos and handles.

FB Logo / BrightHarvestShop
IG Logo / BrightHarvestShop
Twitter Logo / VisitBrightHarvest

When done I'll need the file in PSD and AI.

Target Market(s)

Surrounding local community

Industry/Entity Type

Retail Health Food Store

Contact Information for Business Card

See brief

Requirements
Must have
• Must be double-sided

```html
<!DOCTYPE html>
<html lang="en">
<head>
<meta charset="utf-8">
<title>Bright Harvest – Business Card</title>
<link href="https://fonts.googleapis.com/css2?family=Outfit:wght@700&family=Barlow+Condensed:wght@600&family=Roboto:wght@400;700&display=swap" rel="stylesheet">
<style>
  :root {
    --stage: #bdbdbd;
    --leaf-green: #58b233;
    --seal-ink: #1f7a38;
    --paper: #f5f5f4;
    --paper-shade: #ebedea;
    --ink: #2f2f2f;
    --white: #f2f5f6;
    --pattern-green: #62b83f;
  }
  * { box-sizing: border-box; margin: 0; padding: 0; }
  html, body {
    width: 1190px; height: 1200px; overflow: hidden;
    background: var(--stage);
    font-family: "Roboto", Arial, sans-serif;
  }
  .card {
    position: absolute; left: 174px; width: 838px; height: 504px;
    border-radius: 28px; overflow: hidden;
  }
  .card--front { top: 63px; background: var(--paper); }
  .card--back { top: 646px; background: var(--leaf-green); }

  .card__texture { position: absolute; inset: 0; }
  .card--front .card__texture {
    background: radial-gradient(ellipse at 30% 50%, var(--paper-shade), var(--paper) 70%);
  }
  .card--back .card__texture {
    background: radial-gradient(ellipse at 50% 50%, var(--pattern-green), var(--leaf-green) 75%);
  }

  /* Front brand block */
  .brand { position: absolute; left: 41px; top: 50px; display: flex; align-items: center; }
  .brand__dot {
    width: 58px; height: 58px; border-radius: 50%;
    background: var(--leaf-green); margin-right: 20px;
  }
  .brand__name {
    font-family: "Outfit", Arial, sans-serif; font-weight: 700;
    font-size: 38px; line-height: 1; color: #111; letter-spacing: -0.3px;
  }
  .brand__tagline {
    font-family: "Barlow Condensed", "Arial Narrow", sans-serif; font-weight: 600;
    font-size: 15px; color: var(--leaf-green); letter-spacing: 1.1px; margin-top: 6px;
  }

  /* Contact list */
  .contact { position: absolute; left: 41px; list-style: none; }
  .contact__item {
    position: absolute; left: 0; display: flex; align-items: flex-start;
    font-size: 20px; line-height: 20px; color: var(--ink); white-space: nowrap;
  }
  .contact__icon {
    width: 31px; height: 31px; border-radius: 50%; background: var(--leaf-green);
    flex: none; margin-right: 5px; display: flex; align-items: center; justify-content: center;
  }
  .contact__icon svg { width: 17px; height: 17px; }
  .contact__item--address { top: 193px; }
  .contact__item--address .contact__icon { margin-top: 2px; }
  .contact__item--phone { top: 261px; align-items: center; }
  .contact__item--email { top: 329px; align-items: center; }
  .contact__item--web { top: 397px; align-items: center; }

  /* Anniversary seal */
  .seal { position: absolute; left: 513px; top: 142px; width: 222px; height: 222px; }
  .seal text { font-family: "Roboto", Arial, sans-serif; font-weight: 700; }

  /* Back */
  .back-brand {
    position: absolute; left: 0; right: 0; top: 90px;
    display: flex; flex-direction: column; align-items: center; color: var(--white);
  }
  .back-brand__dot {
    width: 150px; height: 150px; border-radius: 50%;
    border: 10px solid var(--white); margin-bottom: 28px;
  }
  .back-brand__name {
    font-family: "Outfit", Arial, sans-serif; font-weight: 700;
    font-size: 56px; line-height: 1; letter-spacing: -0.5px;
  }
  .back-brand__tagline {
    font-family: "Barlow Condensed", "Arial Narrow", sans-serif; font-weight: 600;
    font-size: 23px; letter-spacing: 1.6px; margin-top: 8px;
  }
  .socials {
    position: absolute; left: 0; right: 0; top: 434px;
    display: flex; justify-content: center; gap: 40px; list-style: none;
  }
  .socials__item {
    display: flex; align-items: center; color: var(--white);
    font-size: 21px; line-height: 1;
  }
  .socials__dot {
    width: 14px; height: 14px; border-radius: 50%;
    background: var(--white); margin-right: 12px;
  }
</style>
</head>
<body>

<section class="card card--front" aria-label="Card front">
  <div class="card__texture" role="img" aria-label="Soft pale botanical swirl pattern"></div>

  <div class="brand">
    <span class="brand__dot"></span>
    <div>
      <div class="brand__name">Bright Harvest</div>
      <div class="brand__tagline">SUPPLEMENTS • HEALTH FOODS • REMEDIES</div>
    </div>
  </div>

  <ul class="contact">
    <li class="contact__item contact__item--address">
      <span class="contact__icon">
        <svg viewBox="0 0 24 24"><path d="M12 2a7 7 0 0 0-7 7c0 5 7 13 7 13s7-8 7-13a7 7 0 0 0-7-7zm0 9.5A2.5 2.5 0 1 1 12 6.5a2.5 2.5 0 0 1 0 5z" fill="#fff"/></svg>
      </span>
      <span>2214 Alder Rd.<br>Linden Falls, CA 95012</span>
    </li>
    <li class="contact__item contact__item--phone">
      <span class="contact__icon">
        <svg viewBox="0 0 24 24"><path d="M6.6 10.8a15 15 0 0 0 6.6 6.6l2.2-2.2a1 1 0 0 1 1-.25 11.4 11.4 0 0 0 3.6.57 1 1 0 0 1 1 1V20a1 1 0 0 1-1 1A17 17 0 0 1 3 4a1 1 0 0 1 1-1h3.5a1 1 0 0 1 1 1c0 1.25.2 2.45.57 3.57a1 1 0 0 1-.25 1z" fill="#fff"/></svg>
      </span>
      <span>707-482-3196</span>
    </li>
    <li class="contact__item contact__item--email">
      <span class="contact__icon">
        <svg viewBox="0 0 24 24" fill="none" stroke="#fff" stroke-width="1.8"><rect x="3" y="7" width="18" height="13" rx="2"/><path d="M9 7V5h6v2M3 12h18M11 12v2h2v-2"/></svg>
      </span>
      <span>BrightHarvestGoods@mailbox-example.com</span>
    </li>
    <li class="contact__item contact__item--web">
      <span class="contact__icon">
        <svg viewBox="0 0 24 24" fill="none" stroke="#fff" stroke-width="1.6"><circle cx="12" cy="12" r="9"/><ellipse cx="12" cy="12" rx="4" ry="9"/><path d="M3 12h18M5 7h14M5 17h14"/></svg>
      </span>
      <span>BrightHarvest.co</span>
    </li>
  </ul>

  <svg class="seal" viewBox="0 0 222 222" aria-label="Celebrating 25 years, 1999 to 2024">
    <defs>
      <path id="seal-top" d="M49 111 A62 62 0 0 1 173 111"/>
      <path id="seal-bottom" d="M31 111 A80 80 0 0 0 191 111"/>
    </defs>
    <circle cx="111" cy="111" r="101" fill="var(--leaf-green)"/>
    <circle cx="111" cy="111" r="91" fill="var(--paper)"/>
    <circle cx="111" cy="111" r="86" fill="none" stroke="var(--leaf-green)" stroke-width="2.5"/>
    <circle cx="111" cy="111" r="52" fill="none" stroke="var(--leaf-green)" stroke-width="2.5"/>
    <circle cx="111" cy="111" r="47" fill="var(--leaf-green)"/>
    <text font-size="20" fill="var(--seal-ink)" letter-spacing="1"><textPath href="#seal-top" startOffset="50%" text-anchor="middle">CELEBRATING</textPath></text>
    <text font-size="22" fill="var(--seal-ink)" letter-spacing="1"><textPath href="#seal-bottom" startOffset="50%" text-anchor="middle">1999 - 2024</textPath></text>
    <text x="38" y="118" font-size="18" fill="var(--leaf-green)" text-anchor="middle">★</text>
    <text x="184" y="118" font-size="18" fill="var(--leaf-green)" text-anchor="middle">★</text>
    <text x="109" y="109" font-size="38" fill="var(--white)" text-anchor="middle">25</text>
    <text x="111" y="135" font-size="22" fill="var(--white)" text-anchor="middle" letter-spacing="-0.5">YEARS</text>
  </svg>
</section>

<section class="card card--back" aria-label="Card back">
  <div class="card__texture" role="img" aria-label="Repeating faint leaf pattern in green tones"></div>

  <div class="back-brand">
    <span class="back-brand__dot"></span>
    <div class="back-brand__name">Bright Harvest</div>
    <div class="back-brand__tagline">SUPPLEMENTS • HEALTH FOODS • REMEDIES</div>
  </div>

  <ul class="socials">
    <li class="socials__item"><span class="socials__dot"></span>BrightHarvestShop</li>
    <li class="socials__item"><span class="socials__dot"></span>BrightHarvestShop</li>
    <li class="socials__item"><span class="socials__dot"></span>VisitBrightHarvest</li>
  </ul>
</section>

</body>
</html>
```